Jolly Dabbers - Face Painting Company requires business card design

Hi,
I am wanting a business card design for a new business in Brisbane (Australia) called 'Jolly Dabbers'. We are a childrens face painting company.

I want to communicate a corporate, simple and clean message through my business card, but also fun and relevant to children.

My company colours are black, yellow and purple, and at the moment I am running with a "cheeky smile" type theme, along the lines of the Fenwick Fox (Tobias and the Glasshouse).

I want this to look Corporate, clean and simple. On the back I would like to see some creative flair with a border or background design, perhaps in white or another colour.

• Front:
Jolly Dabbers
Face Painting Designs

Back:
Maren Ellwick
Artist
0491 283 046
maren@jollydabbers.com.au
www.jollydabbers.com.au
• Attached is the banner which i had made, the business card should go along with this type of theme.
I would like to use the colours Yellow, Black and Purple. Purple should be used in a miniml way, with yellow and black as the main colours.
I want it to have a CORPORATE look.

A Playfull but readable text.

I would like a mix up of the colours on the back in the text.
Maren Ellwick (black)
Artist(purple) etc.

```html
<!DOCTYPE html>
<html lang="en">
<head>
<meta charset="utf-8">
<title>Jolly Dabbers – Business Card</title>
<link rel="stylesheet" href="https://fonts.googleapis.com/css2?family=Josefin+Sans:wght@400;600&family=Righteous&display=swap">
<style>
  :root {
    --backdrop: #e6e2dc;
    --card-yellow: #f3ee55;
    --card-white: #ffffff;
    --ink-black: #111111;
    --ink-purple: #733f98;
    --swirl-white: rgba(255, 255, 255, 0.85);
    --swirl-yellow: rgba(243, 232, 110, 0.75);
    --card-shadow: 0 6px 14px rgba(0, 0, 0, 0.28);
  }
  html, body {
    margin: 0;
    padding: 0;
    width: 1200px;
    height: 802px;
    overflow: hidden;
    background: var(--backdrop);
  }
  .sheet {
    position: relative;
    width: 1200px;
    height: 802px;
  }
  .card {
    position: absolute;
    width: 556px;
    height: 338px;
    overflow: hidden;
    box-shadow: var(--card-shadow);
  }
  .card--front {
    left: 102px;
    top: 52px;
    background: var(--card-yellow);
    border-radius: 0 44px 0 44px;
  }
  .card--back {
    left: 544px;
    top: 410px;
    background: var(--card-white);
    border-radius: 44px 0 44px 0;
  }
  .flourish {
    position: absolute;
  }
  .flourish--front {
    left: 0;
    top: 0;
    width: 300px;
    height: 338px;
    background: radial-gradient(ellipse at 30% 80%, var(--swirl-white) 0%, rgba(255,255,255,0.35) 45%, rgba(255,255,255,0) 75%);
  }
  .flourish--back {
    right: 0;
    top: 0;
    width: 320px;
    height: 338px;
    background: radial-gradient(ellipse at 75% 60%, var(--swirl-yellow) 0%, rgba(243,232,110,0.3) 45%, rgba(243,232,110,0) 75%);
  }
  .brand-name {
    position: absolute;
    left: 30px;
    top: 116px;
    margin: 0;
    font-family: "Righteous", sans-serif;
    font-weight: 400;
    font-size: 50px;
    letter-spacing: 1px;
    color: var(--ink-black);
    line-height: 1;
  }
  .brand-tagline {
    position: absolute;
    left: 70px;
    top: 176px;
    margin: 0;
    font-family: "Righteous", sans-serif;
    font-size: 27px;
    letter-spacing: 2px;
    color: var(--ink-purple);
    line-height: 1;
  }
  .contact {
    position: absolute;
    left: 30px;
    top: 122px;
    margin: 0;
    font-family: "Josefin Sans", sans-serif;
    font-style: normal;
  }
  .contact__name {
    margin: 0;
    font-weight: 600;
    font-size: 40px;
    color: var(--ink-black);
    line-height: 1.1;
  }
  .contact__role {
    margin: 0 0 32px;
    font-family: "Righteous", sans-serif;
    font-size: 34px;
    letter-spacing: 2px;
    color: var(--ink-purple);
    line-height: 1;
  }
  .contact__line {
    margin: 0;
    font-size: 22px;
    font-weight: 400;
    color: var(--ink-black);
    line-height: 28px;
  }
</style>
</head>
<body>
  <main class="sheet">
    <section class="card card--front" aria-label="Business card front">
      <div class="flourish flourish--front" role="img" aria-label="White swirling flourish ornament"></div>
      <h1 class="brand-name">JOLLY DABBERS</h1>
      <p class="brand-tagline">FACE PAINTING DESIGNS</p>
    </section>

    <section class="card card--back" aria-label="Business card back">
      <div class="flourish flourish--back" role="img" aria-label="Pale yellow swirling flourish ornament"></div>
      <address class="contact">
        <p class="contact__name">Maren Ellwick</p>
        <p class="contact__role">ARTIST</p>
        <p class="contact__line">0491 283 046</p>
        <p class="contact__line">maren@jollydabbers.com.au</p>
        <p class="contact__line">www.jollydabbers.com.au</p>
      </address>
    </section>
  </main>
</body>
</html>
```